Brell Stone Company Business Cards

Front and Back Business Card - logo and text setup - cool design. I need workable photoshop or illustrator files so I can setup each employee card with design that is created
Updates

Hi everyone, thank you for the great entries. Please no more white and blue cards - there are so many already - black and silver only now please. thanks!

Target Market(s)

Construction Industry - Facility Managers

Industry/Entity Type

Construction

Contact Information for Business Card

I really like contemporary simplistic looks - clean neat....not opposed to seeing some black backrounds

Requirements
Must have
• Logo/website address with design on front only - www.brellstone-example.com (logo attached)
• Back:
• Name/Title/Company Address/Phone/email address
Nice to have
• Cool design
Should not have
• Nothing gimmicky like Fire or Water - since we are a Fire Protection company - it has all been done

```html
<!DOCTYPE html>
<html lang="en">
<head>
<meta charset="utf-8">
<title>Brell Stone Company Business Cards</title>
<link rel="stylesheet" href="https://fonts.googleapis.com/css2?family=Roboto:wght@400;500;700&display=swap">
<style>
  :root {
    --page-bg: #e4e4e4;
    --card-black: #1b1c1e;
    --silver: #c9ccd1;
    --silver-light: #e6e8eb;
    --silver-dark: #8c9096;
    --text-silver: #b4b8be;
  }
  * { margin: 0; padding: 0; box-sizing: border-box; }
  html, body {
    width: 1125px; height: 1200px; overflow: hidden;
    background: var(--page-bg);
    font-family: "Roboto", Arial, sans-serif;
  }
  .card {
    position: absolute; left: 156px; width: 824px; height: 470px;
    background: var(--card-black);
  }
  .card-front { top: 106px; }
  .card-back { top: 639px; }

  /* Front: name mark and website */
  .front-mark {
    position: absolute; left: 0; right: 0; top: 170px; text-align: center;
    font-weight: 700; font-size: 84px; line-height: 1;
    color: var(--silver); letter-spacing: -1px;
  }
  .front-web {
    position: absolute; left: 0; right: 0; top: 280px; text-align: center;
    font-size: 20px; letter-spacing: 1px; color: var(--text-silver);
  }

  /* Back: person and contact details */
  .back-company {
    position: absolute; left: 52px; top: 58px;
    font-weight: 700; font-size: 58px; line-height: 1;
    color: var(--silver); letter-spacing: -0.5px;
  }
  .person { position: absolute; left: 50px; top: 305px; }
  .person-name {
    font-weight: 500; font-size: 29px; line-height: 1.1; color: var(--silver-light);
  }
  .person-title {
    font-size: 20px; line-height: 1.2; color: var(--silver-dark);
  }
  .address {
    position: absolute; left: 500px; top: 240px;
    font-size: 19px; line-height: 25px; color: var(--text-silver);
  }
  .contact-list {
    position: absolute; left: 500px; top: 308px; list-style: none;
    font-size: 19px; color: var(--text-silver);
  }
  .contact-list li {
    display: flex; align-items: center; height: 26px; white-space: nowrap;
  }
  .contact-list svg {
    width: 17px; height: 17px; margin-right: 14px; fill: var(--silver); flex: none;
  }
  .stripe { position: absolute; bottom: 0; height: 17px; }
  .stripe-dark { left: 0; width: 483px; background: var(--silver-dark); }
  .stripe-light { left: 486px; right: 0; background: var(--silver); }
</style>
</head>
<body>
  <section class="card card-front">
    <div class="front-mark">Brell Stone</div>
    <div class="front-web">www.brellstone-example.com</div>
  </section>

  <section class="card card-back">
    <div class="back-company">Brell Stone</div>

    <div class="person">
      <div class="person-name">Daniel Marsh</div>
      <div class="person-title">CEO/Founder</div>
    </div>

    <div class="address">
      48 Harbor Works Lane<br>
      Millbrook, NY 11500
    </div>

    <ul class="contact-list">
      <li>
        <svg viewBox="0 0 24 24" aria-hidden="true"><path d="M6.6 10.8a15.1 15.1 0 0 0 6.6 6.6l2.2-2.2c.3-.3.7-.4 1-.2 1.1.4 2.3.6 3.6.6.6 0 1 .4 1 1V20c0 .6-.4 1-1 1A17 17 0 0 1 3 4c0-.6.4-1 1-1h3.5c.6 0 1 .4 1 1 0 1.3.2 2.5.6 3.6.1.3 0 .7-.2 1z"/></svg>
        (555) 014-2290
      </li>
      <li>
        <svg viewBox="0 0 24 24" aria-hidden="true"><path d="M7 2h10v5H7zM4 8h16a2 2 0 0 1 2 2v6h-4v-3H6v3H2v-6a2 2 0 0 1 2-2zm3 6h10v8H7z"/></svg>
        (555) 014-2291
      </li>
      <li>
        <svg viewBox="0 0 24 24" aria-hidden="true"><path d="M2 5h20v14H2zm2 2v.5l8 5.5 8-5.5V7zm0 3v7h16v-7l-8 5.5z"/></svg>
        info@brellstone-example.com
      </li>
    </ul>

    <div class="stripe stripe-dark"></div>
    <div class="stripe stripe-light"></div>
  </section>
</body>
</html>
```